LEARN Business Skills so you can Earn a good living

size of the poster is 8”x 10.75" plus 0.25" bleed.
Please leave 1 inch on the bottoum for footer
I want a design a poster that will attract people's attention.
I appreciate a creative ad however the ad should not take away from being able to clearly read the text.
-I also appreciate a simple creative ad that is not too busy.
-you can use graphics, vectors, or pictures of real people.
-however, if you use real people it should be a white male that is wearing a white shirt and look like a professional person.

Target Market(s)

Potential young business people

Industry/Entity Type

education

Requirements
Must have
• easy to read the text
Nice to have
• I would like a "creative" simple ad that is easy to be read
Should not have
• pictures of women

```html
<!DOCTYPE html>
<html lang="en">
<head>
<meta charset="UTF-8">
<title>Rise Up Academy – Business Enrichment Course</title>
<link href="https://fonts.googleapis.com/css2?family=Montserrat:wght@400;500;600;700&display=swap" rel="stylesheet">
<style>
  :root{
    --page:#e9e9ea;
    --navy:#22203f;
    --navy-deep:#1c1a36;
    --plum:#4a2c4a;
    --gold:#e8a42a;
    --orange:#e9822a;
    --yellow:#f0c419;
    --ink:#f3f0f5;
    --ink-soft:#e4e0ea;
  }
  *{box-sizing:border-box;margin:0;padding:0}
  html,body{width:1200px;height:1200px;overflow:hidden}
  body{background:var(--page);font-family:"Montserrat",sans-serif;position:relative}

  .poster{
    position:absolute;left:195px;top:30px;width:810px;height:1140px;overflow:hidden;
    background:
      radial-gradient(circle at 78% 30%, rgba(140,70,70,.55) 0, rgba(90,45,75,.35) 22%, rgba(34,32,63,0) 45%),
      radial-gradient(circle at 0% 100%, rgba(110,50,60,.6) 0, rgba(34,32,63,0) 28%),
      radial-gradient(circle at 100% 70%, rgba(120,60,60,.35) 0, rgba(34,32,63,0) 30%),
      var(--navy);
  }

  .brand{position:absolute;left:42px;top:72px;color:var(--ink);font-weight:700;
    font-size:46px;line-height:50px;letter-spacing:1px;text-transform:uppercase}

  .title{position:absolute;left:27px;top:290px;color:var(--gold);font-weight:700;
    font-size:55px;line-height:61px;letter-spacing:.5px}
  .tagline{position:absolute;left:27px;top:488px;color:var(--ink);font-weight:400;
    font-size:23px;line-height:32px}

  .photo{position:absolute;left:425px;top:245px;width:388px;height:388px}

  .chevrons{position:absolute;left:345px;top:585px}

  .skills-heading{position:absolute;left:35px;top:613px;color:var(--ink);font-weight:600;
    font-size:27px;line-height:38px}

  .benefits{position:absolute;left:40px;top:715px;list-style:none}
  .benefit{display:flex;align-items:center;height:72px;margin-bottom:30px;color:var(--ink);
    font-weight:600;font-size:20px;line-height:27px}
  .benefit svg{width:72px;height:72px;margin-right:14px;flex:none}

  .topics{position:absolute;left:397px;top:690px;width:358px;height:342px;border-radius:18px;
    background:linear-gradient(150deg, rgba(30,28,60,.95) 0%, rgba(38,34,68,.95) 60%, rgba(110,75,80,.6) 100%);
    padding:32px 10px 0;text-align:center;color:var(--ink-soft);font-size:15.2px;line-height:29px;font-weight:400}
  .topics .dot{color:var(--orange)}
</style>
</head>
<body>
  <main class="poster">
    <div class="brand">Rise Up<br>Academy</div>

    <h1 class="title">BUSINESS<br>ENRICHMENT<br>COURSE</h1>
    <p class="tagline">A proven success of helping<br>people in their livelihoods</p>

    <svg class="photo" viewBox="0 0 388 388" role="img" aria-label="Photo of a smiling professional man in a white shirt holding a tablet">
      <defs>
        <linearGradient id="ring" x1="0" y1="0" x2="1" y2="1">
          <stop offset="0" stop-color="#f0c419"/><stop offset="1" stop-color="#e9822a"/>
        </linearGradient>
        <radialGradient id="fill" cx=".5" cy=".45" r=".6">
          <stop offset="0" stop-color="#f4f2f2"/><stop offset="1" stop-color="#d9d6dc"/>
        </radialGradient>
      </defs>
      <circle cx="194" cy="194" r="186" fill="url(#fill)" stroke="url(#ring)" stroke-width="9"/>
    </svg>

    <svg class="chevrons" width="60" height="34" viewBox="0 0 60 34" aria-hidden="true">
      <path d="M4 4l12 13L4 30" fill="none" stroke="#3b3155" stroke-width="5"/>
      <path d="M22 4l12 13-12 13" fill="none" stroke="#5a3f5c" stroke-width="5"/>
      <path d="M40 4l12 13-12 13" fill="none" stroke="#8a5a5e" stroke-width="5"/>
    </svg>

    <h2 class="skills-heading">BUSINESS SKILLS<br>THAT WILL HELP YOU:</h2>

    <ul class="benefits">
      <li class="benefit">
        <svg viewBox="0 0 72 72" aria-hidden="true" fill="none" stroke="#f3f0f5" stroke-width="2.5">
          <circle cx="36" cy="36" r="33"/>
          <circle cx="24" cy="32" r="8"/>
          <path d="M10 58c2-10 8-16 14-16s12 6 14 16"/>
          <path d="M44 48v12M50 44v16M56 48v10"/>
          <path d="M48 6l4 8 8 1-6 6 2 8-8-4-8 4 2-8-6-6 8-1z" fill="#f0a21a" stroke="none"/>
        </svg>
        Get a Quality Job
      </li>
      <li class="benefit">
        <svg viewBox="0 0 72 72" aria-hidden="true" fill="none" stroke="#f3f0f5" stroke-width="2.5">
          <circle cx="16" cy="16" r="11" fill="#f0a21a" stroke="none"/>
          <path d="M10 20l5-5 4 3 6-6" stroke="#22203f"/>
          <path d="M6 46h60l-4 10H10z"/>
          <path d="M8 62h56"/>
          <path d="M40 46V10M40 22c-6 0-8-6-8-10 6 0 8 5 8 10zM40 22c6 0 8-6 8-10-6 0-8 5-8 10zM40 34c-6 0-10-4-10-8 6 0 10 3 10 8zM40 34c6 0 10-4 10-8-6 0-10 3-10 8z"/>
          <path d="M22 46v-8c-5 0-8-3-8-6 5 0 8 3 8 6"/>
        </svg>
        Start/Grow<br>Your Business
      </li>
      <li class="benefit">
        <svg viewBox="0 0 72 72" aria-hidden="true" fill="none" stroke="#f3f0f5" stroke-width="2.5">
          <path d="M8 64l20-22 10 8 22-28"/>
          <path d="M50 20h12v12"/>
          <path d="M8 64h54V40"/>
          <path d="M14 6l2 5 5 2-5 2-2 5-2-5-5-2 5-2zM26 10l1.5 3.5 3.5 1.5-3.5 1.5L26 20l-1.5-3.5-3.5-1.5 3.5-1.5zM18 22l1.5 3.5 3.5 1.5-3.5 1.5L18 32l-1.5-3.5-3.5-1.5 3.5-1.5z" fill="#f0a21a" stroke="none"/>
        </svg>
        Increase Your<br>Salary
      </li>
    </ul>

    <section class="topics">
      <div>Business Administration <span class="dot">•</span> Small</div>
      <div>Business Management <span class="dot">•</span> Finance <span class="dot">•</span></div>
      <div>Investments <span class="dot">•</span> Computers <span class="dot">•</span> Accounting <span class="dot">•</span></div>
      <div>Sales Marketing <span class="dot">•</span> Project Management</div>
      <div>Interviewing Skills <span class="dot">•</span> Business Law <span class="dot">•</span></div>
      <div>Negotiation <span class="dot">•</span> Public Speaking <span class="dot">•</span></div>
      <div>Import/Export <span class="dot">•</span> Information Technoloy <span class="dot">•</span></div>
      <div>Distribution <span class="dot">•</span> Marketing <span class="dot">•</span> Ledgerbook <span class="dot">•</span></div>
      <div>Real Estate <span class="dot">•</span> Health Care <span class="dot">•</span> Management</div>
      <div><span class="dot">•</span> Riverstore</div>
    </section>
  </main>
</body>
</html>
```